Maple Grove Youngsters Guild Business Card Project

We are a Minneapolis based discount club that caters to families with children. We need a business card that can be used to communicate our contact information to other businesses that may wish to offer discounts on our website.

Please use placeholders for contact information (i.e. John Doe, 123 Any Street, Any Town, etc.) and include spaces for the following: Full name, title, email, phone number, website, one line street address, city, state, and zip code.
Updates

Project Deadline Extended
Reason: I have extended the deadline because I had not intended the project to close so quickly.

Target Market(s)

Most of the time the business cards will be used in business to business situations. However, from time to time they may be distributed to our end customer, families with children.

Industry/Entity Type

Club

Font styles to use
Serif
Sans Serif
Other font styles liked:
• Open to suggestions

Requirements
Nice to have
• We might use the reverse side of the card as the design for our membership card.

```html
<!DOCTYPE html>
<html lang="en">
<head>
<meta charset="utf-8">
<title>Maple Grove Youngsters Guild — Business Card</title>
<link href="https://fonts.googleapis.com/css2?family=Arimo:wght@400;700&display=swap" rel="stylesheet">
<style>
  :root {
    --backdrop: #d9d6d2;
    --card-black: #141414;
    --panel-dark: #2a2a2a;
    --panel-light: #4a4a4a;
    --frame-orange: #f0a020;
    --frame-deep: #7a4a0c;
    --name-red: #e3261f;
    --title-gold: #f2b01e;
    --text-light: #f1f1f1;
    --brand-orange: #f5a623;
  }
  * { box-sizing: border-box; margin: 0; padding: 0; }
  html, body { width: 1200px; height: 576px; overflow: hidden; }
  body {
    background: var(--backdrop);
    font-family: "Arimo", Arial, sans-serif;
    display: flex;
    align-items: center;
    justify-content: center;
    gap: 50px;
  }
  .card {
    position: relative;
    width: 520px;
    height: 300px;
    background: var(--card-black);
    border-radius: 6px;
    overflow: hidden;
    box-shadow: 0 8px 24px rgba(0,0,0,.25);
  }
  .card__frame-pattern {
    position: absolute;
    inset: 0;
    background: radial-gradient(ellipse at center, var(--frame-deep) 0%, #3a2308 55%, var(--card-black) 100%);
  }
  .card__panel {
    position: absolute;
    inset: 30px 28px;
    border: 2px solid var(--frame-orange);
    border-radius: 70px 110px 110px 70px;
    background: linear-gradient(160deg, var(--panel-light) 0%, var(--panel-dark) 45%, #1b1b1b 100%);
  }
  .brand {
    position: absolute;
    display: flex;
    align-items: center;
    gap: 10px;
    color: var(--brand-orange);
    font-weight: 700;
    font-size: 24px;
    line-height: 1.1;
  }
  .brand__dot {
    width: 16px; height: 16px;
    border-radius: 50%;
    background: var(--brand-orange);
    flex: none;
  }
  .card--front .brand { left: 70px; top: 110px; width: 300px; }
  .card--back .brand { right: 52px; bottom: 62px; width: 190px; font-size: 20px; }

  .contact {
    position: absolute;
    left: 58px;
    top: 48px;
    color: var(--text-light);
  }
  .contact__name { color: var(--name-red); font-size: 22px; font-weight: 400; }
  .contact__title {
    color: var(--title-gold);
    font-size: 13px;
    margin-top: 3px;
    padding-bottom: 6px;
    border-bottom: 1px solid var(--title-gold);
    width: 250px;
  }
  .contact__list { list-style: none; margin-top: 10px; }
  .contact__item {
    display: flex; align-items: center; gap: 8px;
    font-size: 12px; line-height: 17px;
  }
  .contact__item svg { width: 12px; height: 12px; flex: none; }
  .contact__web { font-size: 13px; margin-top: 8px; }
</style>
</head>
<body>

  <section class="card card--front" aria-label="Card front">
    <div class="card__frame-pattern" role="img" aria-label="Orange sunburst line pattern around the border"></div>
    <div class="card__panel"></div>
    <div class="brand"><span class="brand__dot"></span><span>Maple Grove Youngsters Guild</span></div>
  </section>

  <section class="card card--back" aria-label="Card back">
    <div class="card__frame-pattern" role="img" aria-label="Orange sunburst line pattern around the border"></div>
    <div class="card__panel"></div>
    <div class="contact">
      <h1 class="contact__name">Daniel Marsh</h1>
      <p class="contact__title">Financial Advisor</p>
      <ul class="contact__list">
        <li class="contact__item">
          <svg viewBox="0 0 12 12"><circle cx="6" cy="6" r="6" fill="#f0a020"/><path d="M3 6.5 6 3.5 9 6.5V9H3Z" fill="#141414"/></svg>
          482 birch lane
        </li>
        <li class="contact__item">
          <svg viewBox="0 0 12 12"><circle cx="6" cy="6" r="6" fill="#f0a020"/><path d="M6 2.5a2.3 2.3 0 0 1 2.3 2.3C8.3 6.6 6 9.5 6 9.5S3.7 6.6 3.7 4.8A2.3 2.3 0 0 1 6 2.5Z" fill="#141414"/></svg>
          lakeview
        </li>
        <li class="contact__item">
          <svg viewBox="0 0 12 12"><circle cx="6" cy="6" r="6" fill="#f0a020"/><rect x="3" y="4" width="6" height="4" fill="#141414"/></svg>
          40718
        </li>
        <li class="contact__item">
          <svg viewBox="0 0 12 12"><circle cx="6" cy="6" r="6" fill="#f0a020"/><rect x="3" y="4" width="6" height="4.2" fill="#141414"/><path d="M3 4 6 6.3 9 4" stroke="#f0a020" stroke-width=".8" fill="none"/></svg>
          daniel@guildmail.com
        </li>
        <li class="contact__item">
          <svg viewBox="0 0 12 12"><circle cx="6" cy="6" r="6" fill="#f0a020"/><path d="M4 3h1.3l.6 1.6-.8.6a4 4 0 0 0 1.7 1.7l.6-.8L9 6.7V8a1 1 0 0 1-1 1A5 5 0 0 1 3 4a1 1 0 0 1 1-1Z" fill="#141414"/></svg>
          03 0226 144 512 8
        </li>
      </ul>
      <p class="contact__web">www.mapleyoungstersguild.com</p>
    </div>
    <div class="brand"><span class="brand__dot"></span><span>Maple Grove Youngsters Guild</span></div>
  </section>

</body>
</html>
```